Coffee and Plastics

I am looking for a completely new site that shows the products we have. Our current site is www.velmorebrothersbeans.com. We are open minded to what designers come up with. Our current site is www.velmorebrothersbeans.com. You can you the information from there to start the site. I need these tabs on the main home page. ( Home, Coffee & Tea, Condiments, and Paper and Plastics, and Contact.) You can take photos and info from my Current site. In products page.
I will be uploading info and photo for paper and plastics.
Look and feel
Each slider illustrates characteristics of the customer's brand and the style your logo design should communicate.

```html
<!DOCTYPE html>
<html lang="en">
<head>
<meta charset="utf-8">
<title>Velmore Brothers Beans</title>
<link rel="stylesheet" href="https://fonts.googleapis.com/css2?family=Anton&family=Open+Sans:ital,wght@0,400;0,600;1,300;1,400;1,600&display=swap">
<style>
:root{
  --bg-dark:#1a0302;
  --bg-glow:#6e3a2e;
  --rust:#8a3520;
  --rust-dark:#5a1e10;
  --badge:#ece7e3;
  --orange:#e54524;
  --olive:#a3ad5a;
  --brick:#7e2c1a;
  --cream:#fff;
  --muted:#9c7a70;
  --foot-text:#a08a84;
}
*{margin:0;padding:0;box-sizing:border-box}
html,body{width:1200px;height:1053px;overflow:hidden;background:var(--bg-dark)}
body{font-family:"Open Sans",sans-serif;color:var(--cream);position:relative}
.hero{position:absolute;left:0;top:0;width:1200px;height:763px;overflow:hidden;
  background:radial-gradient(ellipse 420px 360px at 420px 400px,var(--bg-glow),#3a1410 55%,var(--bg-dark) 100%)}
.hero-photo{position:absolute;left:563px;top:326px;width:637px;height:437px;
  background:linear-gradient(135deg,#e6e4e2 0%,#bdb6b2 35%,#4a2a20 65%,#1e0a07 100%)}
.logo-badge{position:absolute;left:482px;top:20px;width:236px;height:236px}
.logo-name{position:absolute;left:482px;top:76px;width:236px;text-align:center;
  font-family:"Anton",sans-serif;color:var(--rust);font-size:28px;line-height:34px;text-transform:lowercase}
.ribbon{position:absolute;top:228px}
.ribbon-left{left:214px}
.ribbon-right{left:886px}
.main-nav{position:absolute;left:280px;top:206px;width:639px;height:64px;background:var(--rust);
  box-shadow:0 8px 14px rgba(0,0,0,.45);display:flex;align-items:center;justify-content:space-between;padding:0 36px}
.main-nav a{font-family:"Anton",sans-serif;font-size:17px;color:var(--cream);text-decoration:none;text-transform:uppercase;letter-spacing:.2px}
.hero-title{position:absolute;left:111px;top:368px;font-family:"Anton",sans-serif;font-size:27px;line-height:36px;font-weight:400;letter-spacing:-.3px}
.hero-lead{position:absolute;left:111px;top:427px;width:430px;font-size:17px;line-height:26px;font-style:italic;font-weight:300;color:var(--muted)}
.read-more{position:absolute;left:111px;top:508px;width:142px;height:66px;background:var(--rust);
  font-family:"Anton",sans-serif;font-size:19px;color:var(--cream);display:flex;align-items:center;justify-content:center;text-decoration:none}
.slide-arrows{position:absolute;left:111px;top:574px;width:103px;height:51px;background:#0e0201;display:flex;align-items:center;justify-content:space-around}
.panels{position:absolute;left:0;top:763px;width:1200px;height:193px;display:flex}
.panel{height:193px;position:relative;padding:30px 0 0 37px}
.panel h2{font-family:"Anton",sans-serif;font-weight:400;font-size:17px;text-transform:uppercase;margin-bottom:12px}
.panel-products{width:309px;background:var(--orange)}
.panel-photo{width:308px;background:linear-gradient(135deg,#6a4a34,#3b2416 60%,#2a170e);padding:0;display:flex;align-items:center;justify-content:center;padding-top:20px;padding-left:18px}
.panel-photo span{font-family:"Anton",sans-serif;font-size:22px;color:#fff;-webkit-text-stroke:2px #2a120b;paint-order:stroke fill;letter-spacing:.2px}
.panel-contact{width:309px;background:var(--olive);padding-left:34px}
.panel-clients{width:274px;background:var(--brick);padding-left:35px}
.product-list{list-style:none}
.product-list li,.contact-list li{font-size:12.5px;font-style:italic;line-height:20.6px}
.contact-list{list-style:none}
.contact-list .phone{font-size:15.5px;font-weight:600;line-height:24px}
.panel-arrows{position:absolute;top:32px;right:30px;display:flex;gap:22px}
.panel-clients .panel-arrows{right:16px}
.client-name{position:absolute;left:0;top:92px;width:274px;text-align:center;font-family:"Open Sans",sans-serif;font-weight:600;font-size:23px;color:var(--cream)}
.client-mark{display:inline-block;width:12px;height:12px;background:var(--cream);margin-right:9px;vertical-align:2px}
.site-footer{position:absolute;left:0;top:956px;width:1200px;height:97px;background:var(--bg-dark)}
.footer-nav{position:absolute;left:34px;top:22px;font-size:12.5px;font-style:italic;color:var(--foot-text)}
.footer-nav a{color:var(--foot-text);text-decoration:none}
.footer-nav .sep{margin:0 8px}
.copyright{position:absolute;left:34px;top:48px;font-size:12.5px;font-style:italic;color:var(--foot-text)}
.copyright strong{font-weight:400;font-style:normal;color:var(--cream)}
.social{position:absolute;right:38px;top:28px;display:flex;gap:2px}
.social span{width:30px;height:30px;border-radius:50%;background:#f2ecea;display:block}
</style>
</head>
<body>
<header class="hero">
  <div class="hero-photo" role="img" aria-label="Photo of a white cup of black coffee seen from above"></div>

  <svg class="ribbon ribbon-left" width="100" height="60" viewBox="0 0 100 60">
    <path d="M0 0H100V60H16C38 44 38 18 0 0Z" fill="var(--rust-dark)"/>
  </svg>
  <svg class="ribbon ribbon-right" width="100" height="60" viewBox="0 0 100 60">
    <path d="M0 0H100C62 18 62 44 84 60H0Z" fill="var(--rust-dark)"/>
  </svg>

  <svg class="logo-badge" viewBox="0 0 236 236">
    <circle cx="118" cy="118" r="118" fill="var(--rust)"/>
    <circle cx="118" cy="118" r="108" fill="var(--badge)"/>
    <circle cx="118" cy="118" r="101" fill="none" stroke="var(--rust)" stroke-width="1.2" stroke-dasharray="1 3"/>
  </svg>
  <div class="logo-name">velmore<br>brothers<br>beans</div>

  <nav class="main-nav">
    <a href="#">Home</a>
    <a href="#">Coffee &amp; Tea</a>
    <a href="#">Condiments</a>
    <a href="#">Paper</a>
    <a href="#">Plastics</a>
    <a href="#">Contact</a>
  </nav>

  <h1 class="hero-title">Coffee Distributor &amp; Contract Packaging</h1>
  <p class="hero-lead">We are a family-owned and operated business based in Brookfield Texas.</p>
  <a class="read-more" href="#">READ MORE</a>
  <div class="slide-arrows">
    <svg width="12" height="20" viewBox="0 0 12 20"><path d="M10 2 2 10l8 8" fill="none" stroke="#fff" stroke-width="2"/></svg>
    <svg width="12" height="20" viewBox="0 0 12 20"><path d="M2 2l8 8-8 8" fill="none" stroke="#fff" stroke-width="2"/></svg>
  </div>
</header>

<section class="panels">
  <div class="panel panel-products">
    <h2>Our Products</h2>
    <div class="panel-arrows">
      <svg width="8" height="14" viewBox="0 0 8 14"><path d="M7 1 1 7l6 6" fill="none" stroke="#fff" stroke-width="1.6"/></svg>
      <svg width="8" height="14" viewBox="0 0 8 14"><path d="M1 1l6 6-6 6" fill="none" stroke="#fff" stroke-width="1.6"/></svg>
    </div>
    <ul class="product-list">
      <li>CAFE SOLANO / 4-Cup Filter Pouch</li>
      <li>CAFE SOLANO / 4-Cup Filter Pouch Pack</li>
      <li>CAFE PRIMO / 1 CUP POD FILTER PACK</li>
      <li>CAFE PRIMO / 1 CUP POD FILTER PACK</li>
      <li>200/cs (Clear Film) 1 regular tea</li>
    </ul>
  </div>
  <div class="panel panel-photo" role="img" aria-label="Photo of a steaming cup of coffee on a wooden table with coffee beans">
    <span>CONDIMENTS, PAPER, PLASTICS</span>
  </div>
  <div class="panel panel-contact">
    <h2>Contact</h2>
    <ul class="contact-list">
      <li>Velmore Brothers</li>
      <li>Brookfield, Texas</li>
      <li>Hours: Monday–Friday, 9:00am–5:00pm (CST)</li>
      <li class="phone">Toll Free Phone:&nbsp; 1-800-555-0142</li>
      <li>E-mail: VelmoreBrothers@example.com</li>
    </ul>
  </div>
  <div class="panel panel-clients">
    <h2>Our Clients</h2>
    <div class="panel-arrows">
      <svg width="8" height="14" viewBox="0 0 8 14"><path d="M7 1 1 7l6 6" fill="none" stroke="#fff" stroke-width="1.6"/></svg>
      <svg width="8" height="14" viewBox="0 0 8 14"><path d="M1 1l6 6-6 6" fill="none" stroke="#fff" stroke-width="1.6"/></svg>
    </div>
    <div class="client-name"><span class="client-mark"></span>Harborline Suites</div>
  </div>
</section>

<footer class="site-footer">
  <nav class="footer-nav">
    <a href="#">Home</a><span class="sep">&nbsp;&nbsp;&nbsp;/&nbsp;&nbsp;&nbsp;</span><a href="#">Coffee &amp; Tea</a><span class="sep">/</span><a href="#">Condiments</a><span class="sep">/</span><a href="#">Paper</a><span class="sep">/</span><a href="#">Plastics</a><span class="sep">/</span><a href="#">Contact</a>
  </nav>
  <p class="copyright">Copyright © 2014 <strong>velmorebrothersbeans</strong>. All rights reserved.</p>
  <div class="social" aria-label="Social links">
    <span></span><span></span><span></span><span></span>
  </div>
</footer>
</body>
</html>
```